Tolvik Commercial Cleaning is lookong for a new business card design.

A fresh new design that's professional and stylish. We need a serious upgrade to our business cards. I have included pictures of our existing ones. Our clients include professional individuals and business owners. We woupdblike something professional and upbeat. Please have fun and see what you come uo with.

Target Market(s)

Property managers, business owners, facility managers and other similar professionals

Industry/Entity Type

Janitorial

Contact Information for Business Card

Name, cell, office number, email, web address

Font styles to use
Sans Serif

Colors

Designer to choose colors to be used in the design.

Requirements
Must have
• please use the green color in our logo
Nice to have
• Bar code
Should not have
• Address

```html
<!DOCTYPE html>
<html lang="en">
<head>
<meta charset="utf-8">
<title>Tolvik Commercial Cleaning – Business Card</title>
<link rel="stylesheet" href="https://fonts.googleapis.com/css2?family=Comfortaa:wght@400;700&family=Roboto:wght@300;400&display=swap">
<style>
  :root {
    --page-bg: #141414;
    --card-bg: #2b2b2b;
    --card-bg-deep: #232323;
    --brand-green: #2db34a;
    --brand-blue: #3a64a8;
    --text-light: #f2f2f2;
    --mark-dark: #1b1b1b;
    --rule: #e6e6e6;
  }
  * { box-sizing: border-box; margin: 0; padding: 0; }
  html, body {
    width: 1200px; height: 963px; overflow: hidden;
    background: var(--page-bg);
  }
  .sheet {
    width: 1200px; height: 963px;
    display: flex; flex-direction: column; align-items: center; justify-content: center;
    gap: 44px;
  }
  .card {
    position: relative;
    width: 735px; height: 420px;
    border-radius: 26px;
    background: radial-gradient(ellipse at 60% 55%, #313131 0%, var(--card-bg) 45%, var(--card-bg-deep) 100%);
    border-bottom: 4px solid var(--brand-green);
    overflow: hidden;
  }

  /* Front */
  .front-identity { position: absolute; left: 58px; top: 58px; }
  .brand-name {
    font-family: "Comfortaa", sans-serif; font-weight: 700;
    font-size: 92px; line-height: 1; letter-spacing: -2px;
    color: var(--brand-green);
  }
  .brand-descriptor {
    font-family: "Comfortaa", sans-serif; font-weight: 700;
    font-size: 27px; color: var(--brand-blue); margin-top: 8px;
  }
  .person-name {
    position: absolute; left: 58px; top: 250px;
    font-family: "Comfortaa", sans-serif; font-weight: 700;
    font-size: 36px; color: var(--brand-green);
  }
  .contact-rule {
    position: absolute; left: 58px; right: 58px; top: 312px;
    height: 1px; background: var(--rule);
  }
  .contact-list {
    position: absolute; left: 58px; right: 58px; top: 330px;
    display: flex; gap: 26px; list-style: none;
    font-family: "Roboto", sans-serif; font-weight: 400;
    font-size: 17px; color: var(--text-light);
  }
  .contact-item { display: flex; align-items: center; gap: 8px; white-space: nowrap; }
  .contact-icon { width: 17px; height: 17px; flex: none; }

  /* Back */
  .back-mark {
    position: absolute; right: -20px; top: -40px;
    font-family: "Comfortaa", sans-serif; font-weight: 700;
    font-size: 250px; line-height: 1; letter-spacing: -8px;
    color: var(--mark-dark);
  }
  .back-descriptor {
    position: absolute; left: 50px; bottom: 86px;
    font-family: "Comfortaa", sans-serif; font-weight: 700;
    font-size: 28px; color: var(--text-light);
  }
  .back-tagline {
    position: absolute; right: 50px; bottom: 40px;
    font-family: "Roboto", sans-serif; font-weight: 300; font-style: italic;
    font-size: 27px; color: var(--brand-green);
  }
</style>
</head>
<body>
<main class="sheet">

  <section class="card card-front" aria-label="Business card front">
    <div class="front-identity">
      <div class="brand-name">tolvik</div>
      <div class="brand-descriptor">tolvik commercial cleaning</div>
    </div>
    <div class="person-name">mara lindqvist</div>
    <div class="contact-rule"></div>
    <ul class="contact-list">
      <li class="contact-item">
        <svg class="contact-icon" viewBox="0 0 24 24" fill="none" stroke="#2db34a" stroke-width="2" stroke-linecap="round" stroke-linejoin="round"><path d="M22 16.9v3a2 2 0 0 1-2.2 2 19.8 19.8 0 0 1-8.6-3.1 19.5 19.5 0 0 1-6-6A19.8 19.8 0 0 1 2.1 4.2 2 2 0 0 1 4.1 2h3a2 2 0 0 1 2 1.7c.1.9.4 1.8.7 2.7a2 2 0 0 1-.5 2.1L8 9.8a16 16 0 0 0 6 6l1.3-1.3a2 2 0 0 1 2.1-.4c.9.3 1.8.6 2.7.7a2 2 0 0 1 1.7 2z"/></svg>
        (555) 014-2290
      </li>
      <li class="contact-item">
        <svg class="contact-icon" viewBox="0 0 24 24" fill="none" stroke="#2db34a" stroke-width="2" stroke-linejoin="round"><rect x="2" y="5" width="20" height="14" rx="1"/><path d="M2 6l10 7 10-7"/></svg>
        mara@tolvikcleaning.com
      </li>
      <li class="contact-item">
        <svg class="contact-icon" viewBox="0 0 24 24" fill="none" stroke="#2db34a" stroke-width="2"><circle cx="12" cy="12" r="10"/><path d="M2 12h20M12 2a15 15 0 0 1 0 20M12 2a15 15 0 0 0 0 20"/></svg>
        www.tolvikcleaning.com
      </li>
    </ul>
  </section>

  <section class="card card-back" aria-label="Business card back">
    <div class="back-mark" aria-hidden="true">tolvik</div>
    <div class="back-descriptor">tolvik commercial cleaning</div>
    <div class="back-tagline">better because we care</div>
  </section>

</main>
</body>
</html>
```